Specialised investor in e-mobility and energy wants business card design

We need a business card design that fits our existing corporate design. <The look and feel must be 'sharp'/'clean', dynamic, communicate momentum, professionalism etc (as one would imagine from a firm in the financial sector). We like the idea of a reverse-side of the card that includes the logo, and the name and contact details on the other. We expect the deliverable to be whatever format might be required to be able to get cards printed directly by a service such as kelmo press. Our website is www.zub.capital

```html
<!DOCTYPE html>
<html lang="en">
<head>
<meta charset="utf-8">
<title>Zub Capital – Business Card</title>
<link href="https://fonts.googleapis.com/css2?family=Roboto:wght@300;400;700&display=swap" rel="stylesheet">
<style>
  :root {
    --backdrop: #9a9a9a;
    --forest: #324f23;
    --leaf: #86b24a;
    --ink-dark: #2c471e;
    --ink-grey: #7a7a7a;
    --rule: #c4c4c4;
    --paper: #ffffff;
  }
  html, body {
    margin: 0;
    padding: 0;
    width: 1200px;
    height: 1000px;
    overflow: hidden;
    background: var(--backdrop);
    font-family: "Roboto", Arial, sans-serif;
  }
  .canvas { position: relative; width: 1200px; height: 1000px; }
  .card {
    position: absolute;
    left: 293px;
    width: 615px;
    height: 351px;
  }
  .card-front { top: 100px; background: var(--forest); }
  .card-back { top: 511px; background: var(--paper); }

  .brand {
    position: absolute;
    left: 0; right: 0;
    display: flex;
    align-items: center;
    justify-content: center;
    gap: 14px;
    font-weight: 400;
  }
  .brand-dot { border-radius: 50%; flex: none; }
  .card-front .brand { top: 145px; font-size: 52px; line-height: 62px; color: var(--paper); }
  .card-front .brand-dot { width: 22px; height: 22px; background: var(--leaf); }
  .card-back .brand { top: 44px; font-size: 30px; line-height: 36px; color: var(--ink-dark); gap: 10px; }
  .card-back .brand-dot { width: 13px; height: 13px; background: var(--leaf); }

  .identity {
    position: absolute;
    right: 333px;
    top: 170px;
    text-align: right;
  }
  .person-name { margin: 0; font-size: 22px; font-weight: 700; color: var(--ink-dark); line-height: 30px; }
  .person-role { margin: 0; font-size: 22px; font-weight: 300; color: var(--leaf); line-height: 30px; }

  .divider {
    position: absolute;
    left: 305px;
    top: 159px;
    width: 2px;
    height: 79px;
    background: var(--rule);
  }

  .contact-list {
    position: absolute;
    left: 328px;
    top: 160px;
    margin: 0;
    padding: 0;
    list-style: none;
  }
  .contact-item {
    display: flex;
    align-items: center;
    gap: 9px;
    height: 26px;
    font-size: 18px;
    color: var(--ink-grey);
  }
  .contact-icon { width: 19px; height: 19px; flex: none; }

  .location {
    position: absolute;
    left: 0; right: 0;
    bottom: 24px;
    margin: 0;
    line-height: 20px;
    text-align: center;
    font-size: 16px;
    color: var(--ink-grey);
  }
</style>
</head>
<body>
<main class="canvas">
  <section class="card card-front">
    <div class="brand"><span class="brand-dot"></span><span class="brand-name">Zub Capital</span></div>
  </section>

  <section class="card card-back">
    <div class="brand"><span class="brand-dot"></span><span class="brand-name">Zub Capital</span></div>

    <div class="identity">
      <p class="person-name">Mark Ellery</p>
      <p class="person-role">Partner</p>
    </div>

    <div class="divider"></div>

    <ul class="contact-list">
      <li class="contact-item">
        <svg class="contact-icon" viewBox="0 0 20 20" aria-hidden="true">
          <rect x="5" y="1" width="10" height="18" rx="2" fill="none" stroke="#86b24a" stroke-width="2"/>
          <circle cx="10" cy="15.5" r="1.2" fill="#86b24a"/>
        </svg>
        <span>+41 70000 4821</span>
      </li>
      <li class="contact-item">
        <svg class="contact-icon" viewBox="0 0 20 20" aria-hidden="true">
          <rect x="1" y="4" width="18" height="12" fill="#86b24a"/>
          <path d="M1 4 L10 11 L19 4" fill="none" stroke="#ffffff" stroke-width="1.4"/>
          <path d="M1 16 L8 9.5 M19 16 L12 9.5" fill="none" stroke="#ffffff" stroke-width="1"/>
        </svg>
        <span>mark@zub.capital</span>
      </li>
      <li class="contact-item">
        <svg class="contact-icon" viewBox="0 0 20 20" aria-hidden="true">
          <circle cx="10" cy="10" r="7.5" fill="#86b24a"/>
          <g fill="none" stroke="#ffffff" stroke-width="0.9">
            <ellipse cx="10" cy="10" rx="3.2" ry="7.5"/>
            <line x1="2.5" y1="10" x2="17.5" y2="10"/>
            <line x1="10" y1="2.5" x2="10" y2="17.5"/>
            <path d="M4 6 H16 M4 14 H16"/>
          </g>
        </svg>
        <span>www.zub.capital</span>
      </li>
    </ul>

    <p class="location">Orvelle, Switzerland</p>
  </section>
</main>
</body>
</html>
```